BRANDEMEIER & BRANDEMEIER,LLP NEEDS A NEW LETTERHEAD DESIGN

a conservative yet contemporary layout befitting a long established
firm, consistent with the times, some form of logo so it catches ones attention, and is
admirable, but portrays integrity
Updates

I would like to approve #22066987 Please advise how to do this as it’s confusing on the site so I can approve payment for the designer

Target Market(s)

real estate investors and building management people

Industry/Entity Type

Law Firm

Font styles to use
Serif

Colors

Designer to choose colors to be used in the design.

Requirements
Must have
• some form of conservative logo

```html
<!DOCTYPE html>
<html lang="en">
<head>
<meta charset="utf-8">
<title>Brandemeier &amp; Brandemeier, LLP — Letterhead</title>
<link href="https://fonts.googleapis.com/css2?family=Cinzel:wght@400;600&family=Arimo:wght@400&display=swap" rel="stylesheet">
<style>
  :root {
    --backdrop: #e4e5e8;
    --paper: #f2f2f2;
    --ink: #1b1b1b;
    --ink-soft: #3a3a3a;
    --silver: #9a9ca2;
    --rule: #7c7c7c;
    --watermark: #e6e8e8;
  }
  html, body {
    margin: 0;
    width: 1200px;
    height: 1166px;
    overflow: hidden;
    background: var(--backdrop);
  }
  .letterhead {
    position: absolute;
    left: 148px;
    top: 0;
    width: 904px;
    height: 1166px;
    background: var(--paper);
  }
  .mark-circle {
    position: absolute;
    left: 408px;
    top: 61px;
    width: 84px;
    height: 84px;
    border: 3px solid var(--silver);
    border-radius: 50%;
    box-sizing: border-box;
  }
  .firm-name {
    position: absolute;
    left: 0;
    right: 0;
    top: 158px;
    margin: 0;
    text-align: center;
    font-family: "Cinzel", serif;
    font-weight: 600;
    font-size: 23px;
    letter-spacing: 0.2px;
    color: var(--ink);
  }
  .header-rule {
    position: absolute;
    left: 292px;
    width: 320px;
    top: 193px;
    height: 1px;
    background: var(--rule);
  }
  .practice-line {
    position: absolute;
    left: 0;
    right: 0;
    top: 197px;
    margin: 0;
    text-align: center;
    font-family: "Cinzel", serif;
    font-size: 10.5px;
    letter-spacing: 0.4px;
    color: var(--ink-soft);
  }
  .watermark {
    position: absolute;
    left: 182px;
    top: 364px;
    width: 540px;
    height: 540px;
  }
  .footer-url {
    position: absolute;
    left: 0;
    right: 0;
    top: 1062px;
    margin: 0;
    text-align: center;
    font-family: "Arimo", sans-serif;
    font-size: 11px;
    letter-spacing: 4px;
    color: var(--ink-soft);
  }
  .footer-rule {
    position: absolute;
    left: 229px;
    width: 446px;
    top: 1089px;
    height: 1px;
    background: var(--rule);
  }
  .footer-contact {
    position: absolute;
    left: 0;
    right: 0;
    top: 1099px;
    margin: 0;
    text-align: center;
    font-family: "Arimo", sans-serif;
    font-style: normal;
    font-size: 11.5px;
    line-height: 15px;
    color: var(--ink-soft);
  }
</style>
</head>
<body>
  <main class="letterhead">
    <header>
      <div class="mark-circle" aria-hidden="true"></div>
      <h1 class="firm-name">Brandemeier &amp; Brandemeier</h1>
      <div class="header-rule"></div>
      <p class="practice-line">New York City Landlord / Tenant Real Estate Law</p>
    </header>

    <svg class="watermark" viewBox="0 0 540 540" aria-hidden="true">
      <circle cx="270" cy="270" r="266" fill="none" stroke="var(--watermark)" stroke-width="6"/>
    </svg>

    <footer>
      <p class="footer-url">www.brandemeierlaw.com</p>
      <div class="footer-rule"></div>
      <address class="footer-contact">
        Brandemeier &amp; Brandemeier, LLP · 418 Harbor Street Suite 210, Brooklyn, New York 11201<br>
        Phone: (718) 555-0142 · Fax: (718)-555-0143 · Email: info@brandemeierlaw.com
      </address>
    </footer>
  </main>
</body>
</html>
```